Help our Sugar Loom find our winning design! We're looking for a business card....

We’re a Sugar Loom in NY specializing in custom-made cakes and unique desserts.
Our cakes combine flavor and art, each designed to match customer’s special event and theme.
We’d like a unique business card with a clean design that will combine French chic and artistic look & feel.
We’d like to differentiate ourselves from standard bakeries, please don’t offer cupcake images :-)
Our logo is peach-pink and brown and we’d love to use these colors ( . Another color that can be added is gold - or feel free to suggest!

Target Market(s)

Women, ages 25-55

Industry/Entity Type

Boutique

Contact Information for Business Card

Text on card:
Logo
Sugar Loom by Dana Welch

www.sugarloomsweets.com
hello@sugarloom.com
(516) 555-0147
F – sugarloomnyc
IG - sugarloom_ny

Font styles to use
Sans Serif
Script

Requirements
Must have
• Logo
• Clean look
• French chic and artistic look & feel.
Nice to have
• Damask pattern
Should not have
• Cupcake images

```html
<!DOCTYPE html>
<html lang="en">
<head>
<meta charset="utf-8">
<title>Sugar Loom business card</title>
<link rel="stylesheet" href="https://fonts.googleapis.com/css2?family=Exo+2:wght@400;600&display=swap">
<style>
  :root {
    --backdrop: #e6e4e2;
    --card: #ffffff;
    --slate: #6b6969;
    --blush: #ef8fa3;
    --ink: #4a4f8f;
    --text: #4c4a4a;
    --soft: #8a8686;
  }
  * { box-sizing: border-box; margin: 0; padding: 0; }
  html, body { width: 1200px; height: 901px; overflow: hidden; }
  body {
    background: var(--backdrop);
    font-family: "Exo 2", sans-serif;
    position: relative;
  }
  .card {
    position: absolute;
    top: 290px;
    width: 540px;
    height: 310px;
    background: var(--card);
    border-radius: 24px;
    overflow: hidden;
    box-shadow: 0 10px 24px rgba(0,0,0,0.14);
  }
  .card--front { left: 50px; }
  .card--back { left: 610px; }
  .front-sweep { position: absolute; inset: 0; width: 100%; height: 100%; }
  .holder {
    position: absolute;
    left: 205px;
    top: 58px;
  }
  .holder__name {
    font-size: 19px;
    font-weight: 600;
    letter-spacing: 1px;
    color: var(--ink);
    text-transform: uppercase;
  }
  .holder__role {
    font-size: 13px;
    color: var(--ink);
    margin-top: 2px;
  }
  .brand {
    position: absolute;
    font-weight: 400;
    color: var(--text);
    letter-spacing: 1px;
    white-space: nowrap;
  }
  .card--front .brand { left: 300px; top: 118px; font-size: 26px; }
  .card--back .brand {
    left: 0; right: 0; top: 130px;
    text-align: center;
    font-size: 36px;
  }
  .contacts {
    position: absolute;
    right: 28px;
    bottom: 24px;
    list-style: none;
    text-align: right;
  }
  .contacts__item {
    display: flex;
    justify-content: flex-end;
    align-items: center;
    gap: 8px;
    font-size: 12px;
    line-height: 18px;
    color: var(--text);
    white-space: nowrap;
  }
  .contacts__item--address { margin-bottom: 4px; }
  .contacts__icon { width: 11px; height: 11px; fill: var(--soft); flex: none; }
  .contacts__spacer { width: 11px; flex: none; }
</style>
</head>
<body>
  <section class="card card--front">
    <svg class="front-sweep" viewBox="0 0 540 310" preserveAspectRatio="none" aria-hidden="true">
      <path d="M0,0 H260 C175,85 150,200 168,310 H0 Z" fill="var(--blush)"/>
      <path d="M0,0 H211 C141,80 111,195 124,310 H0 Z" fill="var(--card)"/>
      <path d="M0,0 H203 C133,80 103,195 116,310 H0 Z" fill="var(--slate)"/>
    </svg>
    <div class="holder">
      <p class="holder__name">Dana Welch</p>
      <p class="holder__role">Managing Director</p>
    </div>
    <p class="brand">Sugar Loom</p>
    <ul class="contacts">
      <li class="contacts__item">214 Mott Street, Suite 3<span class="contacts__spacer"></span></li>
      <li class="contacts__item contacts__item--address">New York, NY 10012<span class="contacts__spacer"></span></li>
      <li class="contacts__item">(516) 555-0147
        <svg class="contacts__icon" viewBox="0 0 12 12"><path d="M2.4 0.5l2 2-1 1.6c.6 1.6 1.9 2.9 3.5 3.5l1.6-1 2 2-1.2 2C4.5 10.6 1.4 7.5 0.4 2.7z"/></svg></li>
      <li class="contacts__item">(516) 555-0182
        <svg class="contacts__icon" viewBox="0 0 12 12"><rect x="3" y="0" width="6" height="12" rx="1"/></svg></li>
      <li class="contacts__item">hello@sugarloom.com
        <svg class="contacts__icon" viewBox="0 0 12 12"><path d="M0 2h12v8H0z M0 2l6 4.5L12 2" stroke="#fff" stroke-width="1"/></svg></li>
      <li class="contacts__item">www.sugarloomsweets.com
        <svg class="contacts__icon" viewBox="0 0 12 12"><circle cx="6" cy="6" r="6"/><path d="M0 6h12M6 0c-3 3-3 9 0 12M6 0c3 3 3 9 0 12" stroke="#fff" stroke-width="0.8" fill="none"/></svg></li>
    </ul>
  </section>

  <section class="card card--back">
    <p class="brand">Sugar Loom</p>
  </section>
</body>
</html>
```